Corvana Tongue Works, LLC

We need a business card that includes information about our business and conveys a reliable business that provides document translation services and interpreters for a variety of corporate and individual clients. We want to come across as professional, reliable, yet approachable. It should include the following on one side:

ESL / ENL Language Classes, Private Lessons, and Online Tutors
PLEXA Training and Testing
Translating & Interpreting Services
Contact us about Over-the-Phone Interpreting in over 200 languages
24/7/365
www.corvanatongue.example

The other side should include (555) 481-3062

Rhoda Pelling, President
482 Garnet Ave., Ste. 219
Indianapolis, IN 40917

Please add USA as part of the address. Also, please add rmpelling@corvanatongueworks.example as the e-mail address. Thank you.

Target Market(s)

Business professionals, their families, the international community

Industry/Entity Type

Business

Contact Information for Business Card

24/7/365
www.corvanatongue.example

(555) 481-3062

Rhoda Pelling, President
482 Garnet Ave., Ste. 219
Indianapolis, IN 40917
USA

Font styles to use
Sans Serif

Colors

Designer to choose colors to be used in the design.

Requirements
Must have
• See project description
• e-mail address and web address
• Phone number
Nice to have
• a globe
• physical address
Should not have
• Should not have the same color scheme as other agencies in our market in Indiana unless it is blue and black. No purple or yellow.

```html
<!DOCTYPE html>
<html lang="en">
<head>
<meta charset="utf-8">
<title>Corvana Tongue Works – Business Card</title>
<link rel="stylesheet" href="https://fonts.googleapis.com/css2?family=Open+Sans:wght@400;600&family=Roboto:wght@400;500&family=Work+Sans:wght@400;500&display=swap">
<style>
  :root {
    --bg: #d9d6d2;
    --ink: #050505;
    --ink-soft: #1c1c1c;
    --blue: #2e97d8;
    --blue-deep: #1f86c9;
    --white: #ffffff;
    --grey-text: #e9e9e9;
  }
  * { margin: 0; padding: 0; box-sizing: border-box; }
  html, body { width: 1200px; height: 930px; overflow: hidden; }
  body {
    background: var(--bg);
    position: relative;
    font-family: "Roboto", Arial, sans-serif;
  }
  .card {
    position: absolute;
    width: 560px;
    height: 320px;
    border-radius: 14px;
    overflow: hidden;
    background: linear-gradient(115deg, var(--ink) 0%, var(--ink) 38%, var(--ink-soft) 50%, var(--ink) 62%, var(--ink) 100%);
    box-shadow: 0 10px 24px rgba(0,0,0,.25);
  }
  .card--front { left: 90px; top: 90px; }
  .card--back { left: 550px; top: 520px; }

  /* front */
  .brand {
    position: absolute; left: 118px; top: 38px;
    display: flex; align-items: center; gap: 18px;
  }
  .brand__circle {
    width: 112px; height: 112px; border-radius: 50%;
    background: var(--white);
  }
  .brand__name {
    font-family: "Open Sans", Arial, sans-serif;
    font-weight: 400; color: var(--blue);
    font-size: 30px; line-height: 1.02;
  }
  .brand__name small { font-size: 16px; }
  .services {
    position: absolute; left: 30px; right: 30px; top: 172px;
    text-align: center; color: var(--white);
    font-weight: 500; font-size: 13.5px; line-height: 1.3;
  }
  .rule {
    height: 1px; background: var(--blue);
    margin: 7px auto;
    width: 88%;
  }
  .services .lead { margin-top: 4px; }

  /* back */
  .sweep { position: absolute; inset: 0; }
  .person {
    position: absolute; left: 34px; top: 124px;
    color: var(--white); font-family: "Work Sans", Arial, sans-serif;
  }
  .person__name {
    color: var(--blue); font-size: 25px; font-weight: 500;
    text-transform: uppercase; letter-spacing: .3px;
  }
  .person__title { font-size: 14px; margin-top: 2px; }
  .person__address { font-size: 14px; line-height: 1.3; margin-top: 18px; }
  .contacts { list-style: none; margin-top: 14px; font-size: 14px; line-height: 1.4; }
  .contacts li { display: flex; align-items: center; gap: 8px; }
  .contacts svg { width: 11px; height: 11px; flex: none; }
  .web-domain { color: var(--blue); }
</style>
</head>
<body>

<section class="card card--front" aria-label="Card front">
  <div class="brand">
    <div class="brand__circle"></div>
    <div class="brand__name">Corvana<br>Tongue Works <small>LLC</small></div>
  </div>
  <div class="services">
    <p>ESL / ENL Language Classes, Private Lessons, and Online Tutors</p>
    <p>PLEXA Training and Testing</p>
    <p>Translating &amp; Interpreting Services</p>
    <div class="rule"></div>
    <p class="lead">Contact us about Over-the-Phone Interpreting in over 200 languages</p>
    <p>24/7/365</p>
  </div>
</section>

<section class="card card--back" aria-label="Card back">
  <svg class="sweep" viewBox="0 0 560 320" aria-hidden="true">
    <path d="M560 0 H300 C300 80 330 190 420 250 C470 285 520 300 560 305 Z" fill="var(--blue)"/>
    <path d="M560 0 H318 C318 80 345 180 430 240 C478 272 522 288 560 292 Z" fill="var(--white)"/>
    <circle cx="455" cy="118" r="98" fill="var(--blue-deep)"/>
    <circle cx="455" cy="118" r="88" fill="none" stroke="var(--white)" stroke-width="3"/>
  </svg>
  <div class="person">
    <h1 class="person__name">Rhoda Pelling</h1>
    <p class="person__title">President</p>
    <p class="person__address">482 Garnet Ave., Ste. 219<br>Indianapolis, IN 40917 USA</p>
    <ul class="contacts">
      <li><svg viewBox="0 0 12 12"><path d="M3 1 L5 3.5 L4 5 Q5.5 7 7 8 L8.5 7 L11 9 L9.5 11 Q5 10.5 1 3 Z" fill="var(--blue)"/></svg>(555) 481-3062</li>
      <li><svg viewBox="0 0 12 12"><rect x="1" y="2.5" width="10" height="7" fill="none" stroke="var(--blue)" stroke-width="1.2"/><path d="M1 2.5 L6 6.5 L11 2.5" fill="none" stroke="var(--blue)" stroke-width="1.2"/></svg>info@corvanatongue.example</li>
      <li><svg viewBox="0 0 12 12"><circle cx="6" cy="6" r="5" fill="none" stroke="var(--blue)" stroke-width="1.1"/><ellipse cx="6" cy="6" rx="2.2" ry="5" fill="none" stroke="var(--blue)" stroke-width="1"/><path d="M1 6 H11" stroke="var(--blue)" stroke-width="1"/></svg>www.<span class="web-domain">corvanatongue.example</span></li>
    </ul>
  </div>
</section>

</body>
</html>
```